Business card design for new eCommerce site focusing on integrity and strong businsess tactics

We need a business card that will stand out and be memorable. Something with color that matches our company logo colors. Think high end version of Pactivo. There are 2 logos provided. The parent company is called Amber Ledge Partners and we are presenting a new and very exciting eCommerce site called BrightHarborTrade.example.

Target Market(s)

Our target markets are in the Activities, Food and Beverage, Health and Beauty

Industry/Entity Type

Marketing

Contact Information for Business Card

We have 4 members that need cards...I will provide all info to the winner of the design contest
Business Address is
4870 West 63rd Avenue, Suite C207
Phoenix AZ 85731

Font styles to use
Serif
Sans Serif

Colors

Designer to choose colors to be used in the design.

Requirements
Must have
• The card must be memorable...should be unique in design but must exude integrity and be playful .
• I have provided several colors or our parent company...please feel free to use which ever
Nice to have
• I will leave this up to you. Feel free to use other images of your choosing that wraps around our client.....Activities, Dining, Health, Beauty
Should not have
• just dont be boring

```html
<!DOCTYPE html>
<html lang="en">
<head>
<meta charset="utf-8">
<title>BrightHarborTrade.example business card</title>
<link rel="stylesheet" href="https://fonts.googleapis.com/css2?family=Questrial&family=Roboto+Condensed:wght@400&family=Arimo:wght@700&display=swap">
<style>
  :root {
    --backdrop: #e9e7e3;
    --card-white: #f7f7f6;
    --brand-blue: #2b7db3;
    --brand-green: #7ac143;
    --text-grey: #555759;
    --divider: #c9c9c9;
    --white: #ffffff;
  }
  * { margin: 0; padding: 0; box-sizing: border-box; }
  html, body {
    width: 1200px; height: 960px; overflow: hidden;
    background: var(--backdrop);
  }
  .canvas { position: relative; width: 1200px; height: 960px; }

  .card {
    position: absolute;
    width: 600px; height: 343px;
    border-radius: 22px;
  }
  .card-front { left: 300px; top: 130px; background: var(--card-white); }
  .card-back  { left: 300px; top: 490px; background: var(--brand-blue); }

  /* Front: brand block */
  .brand {
    position: absolute; left: 46px; top: 152px;
    display: flex; flex-direction: column;
  }
  .brand-row { display: flex; align-items: center; gap: 8px; }
  .brand-dot {
    width: 22px; height: 22px; border-radius: 50%;
    background: var(--brand-blue);
  }
  .brand-name {
    font-family: "Questrial", sans-serif;
    font-size: 18px; color: var(--brand-green);
  }
  .brand-tagline {
    margin: 4px 0 0 30px;
    font-family: "Questrial", sans-serif;
    font-size: 11px; letter-spacing: 0.9px; color: var(--text-grey);
  }

  .divider {
    position: absolute; left: 323px; top: 80px;
    width: 1px; height: 186px; background: var(--divider);
  }

  /* Front: contact block */
  .contact { position: absolute; left: 348px; top: 84px; }
  .person-name {
    font-family: "Roboto Condensed", sans-serif;
    font-size: 25px; color: var(--brand-blue); line-height: 1.1;
  }
  .person-role {
    font-family: "Questrial", sans-serif;
    font-size: 15px; color: var(--brand-green); margin-top: 1px;
  }
  .address {
    font-family: "Questrial", sans-serif;
    font-size: 14px; color: var(--text-grey);
    line-height: 19px; margin-top: 13px;
  }
  .contact-list { list-style: none; margin-top: 8px; }
  .contact-item {
    display: flex; align-items: center; gap: 8px;
    font-family: "Questrial", sans-serif;
    font-size: 14px; color: var(--text-grey); line-height: 19.5px;
  }
  .contact-icon { width: 13px; height: 13px; flex: none; }
  .contact-icon path, .contact-icon circle, .contact-icon rect { fill: var(--brand-blue); }

  /* Back */
  .back-mark {
    position: absolute; left: 260px; top: 80px;
    width: 80px; height: 80px; border-radius: 50%;
    border: 4px solid var(--white);
  }
  .parent-name {
    position: absolute; left: 0; right: 0; top: 216px;
    text-align: center;
    font-family: "Arimo", sans-serif; font-weight: 700;
    font-size: 34px; color: var(--white);
  }
</style>
</head>
<body>
<div class="canvas">

  <section class="card card-front">
    <div class="brand">
      <div class="brand-row">
        <span class="brand-dot"></span>
        <span class="brand-name">BrightHarborTrade.example</span>
      </div>
      <span class="brand-tagline">Outings-Meals-Wellness-Style</span>
    </div>

    <div class="divider"></div>

    <div class="contact">
      <p class="person-name">DANA WHITFIELD</p>
      <p class="person-role">CEO/FOUNDER</p>
      <p class="address">4870 West 63rd Avenue<br>Suite C207, Phoenix AZ 85731</p>
      <ul class="contact-list">
        <li class="contact-item">
          <svg class="contact-icon" viewBox="0 0 16 16"><path d="M3.5 1 6 3.6 4.8 5.6c.9 2 2.6 3.7 4.6 4.6l2-1.2L14 11.5 12.6 14C7 14 2 9 2 3.4Z"/></svg>
          602 555 0148
        </li>
        <li class="contact-item">
          <svg class="contact-icon" viewBox="0 0 16 16"><path d="M4 1h8v14H4Zm1.5 1.5v9h5v-9Zm2.5 10a.9.9 0 1 0 0 1.8.9.9 0 0 0 0-1.8Z"/></svg>
          602 555 0172
        </li>
        <li class="contact-item">
          <svg class="contact-icon" viewBox="0 0 16 16"><path d="M1 3.5h14v9H1Zm1.4 1.2L8 8.8l5.6-4.1Z"/></svg>
          dana@brightharbortrade.example
        </li>
        <li class="contact-item">
          <svg class="contact-icon" viewBox="0 0 16 16"><circle cx="8" cy="8" r="7"/></svg>
          www.brightharbortrade.example
        </li>
      </ul>
    </div>
  </section>

  <section class="card card-back">
    <span class="back-mark"></span>
    <p class="parent-name">Amber Ledge Partners</p>
  </section>

</div>
</body>
</html>
```